8x8 Social Media Ad - Brant Summit Expo

Attention Real Estate Agents
Please join us for our
Quarterly Real Estate Training Expo
The 2nd Saturday of February, May, August and November
Our Next Training Expo is _________________________________
From 9 am to 1 pm
at
Halvorne Suites Millbrook Court
4817 Copper Willow Lane, Dunmere, MD 20588
Scheduled Speakers
9:00 am - Marcus Pellington - Orientation
9:30 am - Derrin Oakfield - Multiple Income Streams / Crest Program
10:00 am - Talia Brennick - Marketing though Social Media
10:45 am - Rex Dunmore - Generating Business through Ru-Plaza
11:30 am - Kemi Adeyoro - Real Estate Investing
12:15 pm - Gregor Tamsey - (Main Speaker) Training Topic TBA
For more information call Marcus Pellington at (240) 555-0183 or email mpellington@brantsummithomes.example

```html
<!DOCTYPE html>
<html lang="en">
<head>
<meta charset="utf-8">
<title>Brant Summit Expo – Quarterly Real Estate Training Expo</title>
<link rel="stylesheet" href="https://fonts.googleapis.com/css2?family=Bebas+Neue&family=Oswald:wght@400;600&family=Montserrat:wght@400;500;600;700;800&family=Allison&display=swap">
<style>
:root{
  --page:#05333b;
  --teal-deep:#0a4a57;
  --teal-mid:#0d7f92;
  --teal-bright:#06d9e8;
  --cyan-blob:#08c6f2;
  --yellow:#ffd20f;
  --navy:#1b3a6b;
  --white:#ffffff;
  --paper:#f1f3f4;
  --ink:#1d1d1f;
  --grey:#555b60;
  --accent-teal:#17a3b4;
  --photo-a:#3a3f48;
  --photo-b:#1f232a;
}
*{margin:0;padding:0;box-sizing:border-box}
html,body{width:1089px;height:1200px;overflow:hidden;background:var(--page)}
.ad{
  position:absolute;left:44px;top:100px;width:1000px;height:1000px;overflow:hidden;
  background:
    radial-gradient(ellipse 60% 45% at 78% 8%, var(--teal-bright) 0%, rgba(6,217,232,0) 70%),
    linear-gradient(160deg, #0c97ad 0%, var(--teal-mid) 35%, var(--teal-deep) 75%, #083f4b 100%);
  font-family:'Montserrat',sans-serif;color:var(--white);
}
.abs{position:absolute}
.brand{left:808px;top:60px;width:180px;display:flex;align-items:center;gap:8px}
.brand-mark{width:14px;height:14px;background:var(--white)}
.brand-name{font-family:'Bebas Neue',sans-serif;font-size:32px;line-height:1;letter-spacing:1px;color:var(--white)}
.attention{left:115px;top:96px;font-family:'Bebas Neue',sans-serif;font-size:31px;line-height:1;white-space:nowrap}
.attention .hl{color:var(--yellow)}
.attention-rule{left:115px;top:143px;width:329px;height:2px;background:var(--yellow)}
.invite{left:100px;top:160px;font-family:'Allison',cursive;font-size:92px;line-height:1;color:var(--yellow);white-space:nowrap}
.kicker{left:104px;top:276px;font-family:'Oswald',sans-serif;font-size:31px;line-height:1;letter-spacing:4.3px;white-space:nowrap}
.title{left:30px;top:312px;font-family:'Bebas Neue',sans-serif;font-size:101px;line-height:1;color:var(--yellow);white-space:nowrap;letter-spacing:.5px}
.ordinal{left:55px;top:441px;font-size:57px;font-weight:800;line-height:1;color:var(--yellow)}
.divider{left:189px;top:445px;width:2px;height:50px;background:var(--white)}
.day{left:201px;top:438px;font-size:44px;font-weight:500;letter-spacing:3.5px;line-height:1}
.months{left:202px;top:485px;font-size:13px;font-weight:600;letter-spacing:.9px;white-space:nowrap}
.next{left:109px;top:538px;font-size:20px;font-weight:400;white-space:nowrap}
.hours{left:166px;top:579px;width:225px;height:52px;border-radius:6px;background:var(--yellow);
  display:flex;align-items:center;justify-content:center;font-family:'Oswald',sans-serif;font-weight:600;font-size:22px;color:var(--navy)}
.main-speaker{left:772px;top:198px;width:200px;text-align:center}
.main-speaker .time,.main-speaker .name{font-size:19px;font-weight:700;line-height:24px}
.main-speaker .name .hl{color:var(--yellow)}
.main-speaker .role{font-size:14px;font-weight:500;line-height:18px}
.main-speaker .role:first-of-type{margin-top:4px}
.pointer{left:858px;top:302px}
.feature{left:515px;top:280px}
.paper{left:0;top:760px}
.lineup{left:0;top:676px;width:1000px;height:230px}
.speaker{position:absolute;top:0;width:170px;margin-left:-85px;text-align:center;color:var(--ink)}
.speaker svg{display:block;margin:0 auto}
.speaker .time,.speaker .name{font-size:14px;font-weight:700;line-height:17px}
.speaker .time{margin-top:7px}
.speaker .topic{font-size:13.5px;font-weight:500;line-height:17px}
.rule-dash{left:0;top:909px;width:1000px;border-top:1px dashed #9ccfd6}
.contact{left:88px;top:930px;display:flex;gap:9px;align-items:center}
.contact-text .lead{font-size:10.5px;line-height:12px;color:var(--grey);letter-spacing:.4px}
.contact-text .phone{font-size:19px;font-weight:700;color:var(--accent-teal);line-height:24px}
.email{left:328px;top:945px;display:flex;gap:11px;align-items:center;font-size:15.5px;color:var(--grey)}
.join{left:735px;top:938px;width:180px;height:42px;border-radius:4px;background:linear-gradient(180deg,#1fb2c2,#138e9f);
  display:flex;align-items:center;justify-content:center;font-size:22px;font-weight:700;color:var(--white)}
</style>
</head>
<body>
<main class="ad">

  <div class="abs brand"><span class="brand-mark"></span><span class="brand-name">BRANT SUMMIT</span></div>

  <p class="abs attention">ATTENTION <span class="hl">REAL ESTATE AGENTS</span></p>
  <div class="abs attention-rule"></div>
  <p class="abs invite">Please join us for our</p>

  <h1>
    <span class="abs kicker">QUARTERLY REAL ESTATE</span>
    <span class="abs title">TRAINING EXPO</span>
  </h1>

  <span class="abs ordinal">2ND</span>
  <span class="abs divider"></span>
  <span class="abs day">SATURDAY</span>
  <span class="abs months">of February, May, August &amp; November</span>

  <p class="abs next">Our Next Training Expo is _______</p>
  <div class="abs hours">From 9 am to 1 pm</div>

  <div class="abs main-speaker">
    <p class="time">12:15 PM</p>
    <p class="name">GREGOR <span class="hl">TAMSEY</span></p>
    <p class="role">(Main Speaker)</p>
    <p class="role">Training Topic TBA</p>
  </div>

  <svg class="abs pointer" width="36" height="52" viewBox="0 0 36 52" fill="none" stroke="#fff" stroke-width="1.6" stroke-linejoin="round">
    <path d="M6 46 L24 14 L18 11 L32 2 L31 18 L26 15 L9 48 Z"/>
  </svg>

  <svg class="abs feature" width="480" height="400" viewBox="0 0 480 400">
    <defs>
      <clipPath id="feature-clip">
        <path d="M0 0 H480 V48 C470 200 420 330 240 384 C120 390 40 340 22 245 C10 160 60 100 150 90 Z"/>
      </clipPath>
      <linearGradient id="photo-grad" x1="0" y1="0" x2="0" y2="1">
        <stop offset="0" stop-color="var(--photo-a)"/>
        <stop offset="1" stop-color="var(--photo-b)"/>
      </linearGradient>
    </defs>
    <path d="M22 245 C8 160 70 105 170 104 C260 104 300 80 380 50 C430 30 465 40 465 110 C465 220 400 330 230 380 C120 395 38 340 22 245 Z" fill="var(--cyan-blob)"/>
    <path d="M14 240 C2 150 75 90 165 90 L270 88 M300 72 C380 40 470 -10 488 100 C500 230 400 360 240 385 C110 400 25 330 14 240" fill="none" stroke="var(--yellow)" stroke-width="1.4"/>
    <g clip-path="url(#feature-clip)" role="img" aria-label="Photo of main speaker Gregor Tamsey in a dark blazer and pink shirt">
      <path d="M95 400 C110 330 160 300 200 290 C170 250 150 200 150 140 C150 60 210 5 290 5 C370 5 430 60 420 160 C415 215 400 255 380 285 C420 305 460 330 480 400 Z" fill="url(#photo-grad)"/>
    </g>
  </svg>

  <svg class="abs paper" width="1000" height="240" viewBox="0 0 1000 240" preserveAspectRatio="none">
    <path d="M0 12 L40 8 L70 16 L110 10 L160 14 L210 6 L260 15 L320 9 L380 16 L440 8 L500 14 L560 7 L620 15 L680 9 L740 16 L800 10 L860 14 L920 6 L960 13 L1000 8 V240 H0 Z" fill="var(--paper)"/>
    <path d="M0 22 L60 18 L140 26 L240 20 L360 27 L480 21 L600 27 L720 20 L840 26 L1000 19 V240 H0 Z" fill="var(--white)" opacity=".7"/>
  </svg>

  <section class="abs lineup" aria-label="Scheduled speakers">
    <div class="speaker" style="left:163px">
      <svg width="140" height="130" viewBox="0 0 140 130">
        <path d="M6 52 C10 28 40 26 70 30 C95 24 115 10 125 16 C140 30 130 100 85 122 C40 135 0 95 6 52 Z" fill="var(--cyan-blob)"/>
        <path d="M4 50 C8 24 40 22 70 26 M96 18 C118 4 138 6 136 36 C132 90 100 128 70 127 C30 126 0 95 4 50" fill="none" stroke="var(--yellow)" stroke-width="1.2"/>
        <path role="img" aria-label="Photo of Marcus Pellington" d="M28 127 C30 90 45 80 55 75 C48 60 50 20 70 0 C90 15 95 60 85 75 C100 82 112 95 115 120 Z" fill="url(#photo-grad)"/>
      </svg>
      <p class="time">09:00 AM</p><p class="name">MARCUS PELLINGTON</p><p class="topic">Orientation</p>
    </div>
    <div class="speaker" style="left:325px">
      <svg width="140" height="130" viewBox="0 0 140 130">
        <path d="M6 52 C10 28 40 26 70 30 C95 24 115 10 125 16 C140 30 130 100 85 122 C40 135 0 95 6 52 Z" fill="var(--yellow)"/>
        <path d="M4 50 C8 24 40 22 70 26 M96 18 C118 4 138 6 136 36 C132 90 100 128 70 127 C30 126 0 95 4 50" fill="none" stroke="var(--teal-deep)" stroke-width="1.2"/>
        <path role="img" aria-label="Photo of Derrin Oakfield" d="M32 127 C32 90 45 80 58 75 C50 55 55 15 72 6 C92 15 95 60 86 75 C100 82 115 95 116 127 Z" fill="url(#photo-grad)"/>
      </svg>
      <p class="time">09:30 AM</p><p class="name">DERRIN OAKFIELD</p><p class="topic">Multiple Income<br>Streams / Crest Program</p>
    </div>
    <div class="speaker" style="left:496px">
      <svg width="140" height="130" viewBox="0 0 140 130">
        <path d="M6 52 C10 28 40 26 70 30 C95 24 115 10 125 16 C140 30 130 100 85 122 C40 135 0 95 6 52 Z" fill="var(--cyan-blob)"/>
        <path d="M4 50 C8 24 40 22 70 26 M96 18 C118 4 138 6 136 36 C132 90 100 128 70 127 C30 126 0 95 4 50" fill="none" stroke="var(--yellow)" stroke-width="1.2"/>
        <path role="img" aria-label="Photo of Talia Brennick" d="M42 127 C44 105 55 98 62 95 C56 80 58 48 75 42 C92 48 95 80 88 95 C98 100 108 110 110 127 Z" fill="url(#photo-grad)"/>
      </svg>
      <p class="time">10:00 AM</p><p class="name">TALIA BRENNICK</p><p class="topic">Marketing though<br>Social Media</p>
    </div>
    <div class="speaker" style="left:661px">
      <svg width="140" height="130" viewBox="0 0 140 130">
        <path d="M6 52 C10 28 40 26 70 30 C95 24 115 10 125 16 C140 30 130 100 85 122 C40 135 0 95 6 52 Z" fill="var(--cyan-blob)"/>
        <path d="M4 50 C8 24 40 22 70 26 M96 18 C118 4 138 6 136 36 C132 90 100 128 70 127 C30 126 0 95 4 50" fill="none" stroke="var(--yellow)" stroke-width="1.2"/>
        <path role="img" aria-label="Photo of Rex Dunmore" d="M22 127 C26 100 40 90 55 85 C48 65 52 22 74 18 C96 22 100 65 92 85 C108 90 122 100 124 127 Z" fill="url(#photo-grad)"/>
      </svg>
      <p class="time">10:45 AM</p><p class="name">REX DUNMORE</p><p class="topic">Generating Business<br>through Ru-Plaza</p>
    </div>
    <div class="speaker" style="left:829px">
      <svg width="140" height="130" viewBox="0 0 140 130">
        <path d="M6 52 C10 28 40 26 70 30 C95 24 115 10 125 16 C140 30 130 100 85 122 C40 135 0 95 6 52 Z" fill="var(--cyan-blob)"/>
        <path d="M4 50 C8 24 40 22 70 26 M96 18 C118 4 138 6 136 36 C132 90 100 128 70 127 C30 126 0 95 4 50" fill="none" stroke="var(--yellow)" stroke-width="1.2"/>
        <path role="img" aria-label="Photo of Kemi Adeyoro in a denim shirt" d="M22 120 C26 95 40 85 55 80 C48 60 52 5 72 0 C94 5 98 60 90 80 C106 85 120 95 124 120 Z" fill="#3d5570"/>
      </svg>
      <p class="time">11:30 AM</p><p class="name">KEMI ADEYORO</p><p class="topic">Real Estate Investing</p>
    </div>
  </section>

  <div class="abs rule-dash"></div>

  <div class="abs contact">
    <svg width="32" height="40" viewBox="0 0 32 40">
      <rect x="2" y="0" width="30" height="40" rx="3" fill="var(--accent-teal)"/>
      <g fill="#0d6f7c"><rect x="0" y="7" width="5" height="3" rx="1"/><rect x="0" y="15" width="5" height="3" rx="1"/><rect x="0" y="23" width="5" height="3" rx="1"/><rect x="0" y="31" width="5" height="3" rx="1"/></g>
      <path d="M12 10 C10 12 10 16 13 21 C16 26 20 29 23 29 L25 26 L21 23 L19 25 C17 24 15 21 14 19 L16 17 L14 12 Z" fill="#fff"/>
    </svg>
    <div class="contact-text">
      <p class="lead">For more information<br>call Marcus Pellington at</p>
      <p class="phone">(240) 555-0183</p>
    </div>
  </div>

  <div class="abs email">
    <svg width="31" height="22" viewBox="0 0 31 22" fill="none" stroke="var(--accent-teal)" stroke-width="2.2">
      <rect x="1.5" y="1.5" width="28" height="19"/><path d="M1.5 1.5 L15.5 12 L29.5 1.5 M1.5 20.5 L12 10 M29.5 20.5 L19 10"/>
    </svg>
    <span>mpellington@brantsummithomes.example</span>
  </div>

  <div class="abs join">Join Now</div>
</main>
</body>
</html>
```